Marwick Law Letterhead

We need a new letterhead design for a Law Firm. The address for the law firm is 1475 Calloway Street, Suite 210, Houston, Texas 77041. Phone Number: 832-361-9027; Fax Number: 832-614-7359. The logo is uploaded to the project.

```html
<!DOCTYPE html>
<html lang="en">
<head>
<meta charset="utf-8">
<title>Marwick Law Letterhead</title>
<link rel="stylesheet" href="https://fonts.googleapis.com/css2?family=Open+Sans:wght@400;600&family=Lato:wght@400&display=swap">
<style>
  :root {
    --navy: #1b2d5a;
    --red: #8c0f18;
    --red-bright: #c21f2a;
    --ink: #3b3b3b;
    --backdrop: #e4e4e4;
    --paper: #ffffff;
    --signature-tone: #e9e9ec;
  }
  * { margin: 0; padding: 0; box-sizing: border-box; }
  html, body { width: 1040px; height: 1200px; overflow: hidden; }
  body { background: var(--backdrop); font-family: "Open Sans", sans-serif; color: var(--ink); }

  .letterhead {
    position: absolute; left: 80px; top: 34px;
    width: 881px; height: 1132px;
    background: var(--paper);
    box-shadow: 0 2px 10px rgba(0,0,0,0.18);
    overflow: hidden;
  }
  .header-bands { position: absolute; left: 0; top: 0; }

  .firm-name {
    position: absolute; right: 124px; top: 56px;
    display: flex; align-items: center; gap: 14px;
    font-family: "Open Sans", sans-serif; font-weight: 600;
    font-size: 34px; color: var(--navy); letter-spacing: 0.5px;
  }
  .firm-mark { width: 44px; height: 44px; background: var(--navy); }

  .block { position: absolute; left: 84px; font-size: 14px; line-height: 17px; }
  .issue-date { top: 211px; }
  .recipient { top: 245px; }
  .salutation { top: 343px; }

  .letter-body { position: absolute; left: 84px; width: 711px; font-size: 14px; line-height: 25.3px; text-align: justify; }
  .para-1 { top: 390px; }
  .para-2 { top: 542px; }
  .para-3 { top: 644px; }

  .closing { top: 775px; }
  .signature { position: absolute; left: 84px; top: 810px; width: 202px; height: 26px; background: var(--signature-tone); border-radius: 4px; }
  .signer-name { position: absolute; left: 84px; top: 848px; font-size: 17px; font-weight: 600; color: #2f2f2f; }
  .signer-title { position: absolute; left: 84px; top: 877px; font-size: 14px; }

  .contact-bar {
    position: absolute; left: 57px; top: 1081px;
    display: flex; align-items: center;
    font-family: "Lato", sans-serif; font-size: 16.5px; color: #1e1e1e;
  }
  .contact-item { display: flex; align-items: center; gap: 4px; margin-right: 4px; }
  .contact-icon { width: 28px; height: 28px; border-radius: 4px; display: flex; align-items: center; justify-content: center; }
  .icon-navy { background: var(--navy); }
  .icon-red { background: var(--red-bright); }
</style>
</head>
<body>
  <main class="letterhead">
    <svg class="header-bands" width="881" height="36" viewBox="0 0 881 36" aria-hidden="true">
      <polygon points="0,0 430,0 412,35 0,35" fill="var(--navy)"/>
      <polygon points="440,0 881,0 881,20 430,20" fill="var(--red)"/>
    </svg>

    <div class="firm-name"><span class="firm-mark"></span>Marwick Law</div>

    <p class="block issue-date">Issuing Date: May 5, 2018</p>
    <p class="block recipient">Name Of Employee Mr. XYZABC<br>Address of Employee<br>Address Line 2 etc..</p>
    <p class="block salutation">Dear Mr.XYZABC</p>

    <p class="letter-body para-1">Lorem Ipsum has been the industry's standard dummy text ever since the 1500s, when an unknown printer took a galley of type and scrambled it to make a type specimen book. It has survived not only five centuries, but also the leap into electronic typesetting, remaining essentially unchanged. It was popularised in the 1960s with the release of Letraset sheets containing Lorem Ipsum passages, and more recently with desktop publishing software like Aldus PageMaker including versions of Lorem Ipsum.</p>
    <p class="letter-body para-2">Lorem Ipsum is simply dummy text of the printing and typesetting industry. Lorem Ipsum has been the industry's standard dummy text ever since the 1500s, when an unknown printer took a galley of type and scrambled it to make a type specimen book.</p>
    <p class="letter-body para-3">It has survived not only five centuries, but also the leap into electronic typesetting, remaining essentially unchanged. It was popularised in the 1960s with the release of Letraset sheets containing Lorem IpsumIpsum passages.</p>

    <p class="block closing">Yours Sincerely</p>
    <div class="signature" role="img" aria-label="Handwritten signature of Daniel Brooks"></div>
    <p class="signer-name">Daniel Brooks</p>
    <p class="signer-title">Managing Director</p>

    <footer class="contact-bar">
      <div class="contact-item">
        <span class="contact-icon icon-navy">
          <svg width="16" height="16" viewBox="0 0 24 24" aria-hidden="true"><path fill="#fff" d="M6.6 10.8a15.1 15.1 0 0 0 6.6 6.6l2.2-2.2a1 1 0 0 1 1-.25 11.4 11.4 0 0 0 3.6.57 1 1 0 0 1 1 1V20a1 1 0 0 1-1 1A17 17 0 0 1 3 4a1 1 0 0 1 1-1h3.5a1 1 0 0 1 1 1c0 1.25.2 2.45.57 3.57a1 1 0 0 1-.25 1z"/></svg>
        </span>832-361-9027
      </div>
      <div class="contact-item">
        <span class="contact-icon icon-red">
          <svg width="16" height="16" viewBox="0 0 24 24" aria-hidden="true"><path fill="#fff" d="M7 3h10v4H7zM4 8h16a2 2 0 0 1 2 2v6h-4v4H6v-4H2v-6a2 2 0 0 1 2-2zm4 7v3h8v-3z"/></svg>
        </span>832-614-7359
      </div>
      <div class="contact-item">
        <span class="contact-icon icon-navy">
          <svg width="16" height="16" viewBox="0 0 24 24" aria-hidden="true"><path fill="#fff" d="M12 2a7 7 0 0 0-7 7c0 5 7 13 7 13s7-8 7-13a7 7 0 0 0-7-7zm0 9.5A2.5 2.5 0 1 1 12 6.5a2.5 2.5 0 0 1 0 5z"/></svg>
        </span>1475 Calloway Street, Suite 210, Houston, Texas 77041
      </div>
    </footer>
  </main>
</body>
</html>
```